Flaschenetiketten-Design in rechteckiger Grundform für Biermanufaktur
Zielgruppe
Wir repräsentieren eine Bier-Manufaktur in der Gründungsphase und sind auf der Suche nach einem Designvorschlag für die Flaschenetiketten.
Unsere Zielgruppe sind Liebhaber, die auf der Suche nach dem Speziellen und Lokalen sind. Der Biergenuss abseits des Massenmarktes soll im Entwurf sichtbar/transportiert werden. Die Bier-Manufaktur steht zeitgleich für Trend-Kreationen mit bodenständigem Ursprung.
Aufgabenstellung
Die Herkunft der Gründer Familie aus dem Schweizer Kanton Simplon soll im Vordergrund stehen, hierzu bitte das Familienwappen / einzelne Elemente siehe Dateiupload berücksichtigen.
Das Etikett soll eine rechteckige Grundform haben.
Folgende Angaben sollen sich im Etikett wiederfinden:
- Biersorte: 'Lager' (zukünftig soll es möglich sein, Biersorte auf dem Etikett zu wechseln)
Brand: 'Hearty Kandrom'
'Biermanufaktur Walliser Ursprungs'
Die Schrift soll klar und nicht zu verspielt sein.

```html
<!DOCTYPE html>
<html lang="de">
<head>
<meta charset="utf-8">
<title>Hearty Kandrom – Lagerbier Etikett</title>
<link rel="stylesheet" href="https://fonts.googleapis.com/css2?family=Josefin+Sans:wght@600;700&display=swap">
<style>
  :root {
    --page-bg: #ffffff;
    --label-navy: #1d2433;
    --label-band: #2b3242;
    --silver-light: #f2f2f2;
    --silver-mid: #b9b9b9;
    --silver-dark: #6d6d6d;
    --text-white: #ffffff;
  }
  html, body {
    margin: 0;
    padding: 0;
    width: 844px;
    height: 1200px;
    overflow: hidden;
    background: var(--page-bg);
  }
  .canvas {
    position: relative;
    width: 844px;
    height: 1200px;
  }
  .bottle-label {
    position: absolute;
    left: 72px;
    top: 211px;
    width: 700px;
    height: 777px;
    box-shadow: 6px 10px 22px rgba(0,0,0,0.35);
    font-family: "Josefin Sans", sans-serif;
    color: var(--text-white);
    text-align: center;
  }
  .label-art {
    position: absolute;
    inset: 0;
    width: 100%;
    height: 100%;
  }
  .crest-area {
    position: absolute;
    left: 233px;
    top: 64px;
    width: 233px;
    height: 281px;
    background: linear-gradient(135deg, var(--silver-dark) 0%, var(--silver-light) 45%, var(--silver-mid) 70%, var(--silver-dark) 100%);
    border-radius: 4px 4px 40% 40% / 4px 4px 18% 18%;
    box-shadow: 0 0 0 3px #8a8a8a;
  }
  .beer-style {
    position: absolute;
    left: 0;
    right: 0;
    top: 364px;
    font-size: 26px;
    font-weight: 600;
    letter-spacing: 2px;
  }
  .brand-name {
    position: absolute;
    left: 0;
    right: 0;
    top: 445px;
    margin: 0;
    font-size: 108px;
    font-weight: 600;
    line-height: 94px;
    letter-spacing: 3px;
  }
  .brewery-line {
    position: absolute;
    left: 0;
    right: 0;
    top: 722px;
    font-size: 20px;
    font-weight: 600;
    letter-spacing: 3.4px;
  }
</style>
</head>
<body>
<div class="canvas">
  <div class="bottle-label">
    <svg class="label-art" viewBox="0 0 765 849" preserveAspectRatio="none" aria-hidden="true">
      <defs>
        <linearGradient id="silverFrame" x1="0" y1="0" x2="1" y2="1">
          <stop offset="0" stop-color="#8a8a8a"/>
          <stop offset="0.4" stop-color="#e8e8e8"/>
          <stop offset="0.7" stop-color="#9a9a9a"/>
          <stop offset="1" stop-color="#d6d6d6"/>
        </linearGradient>
        <linearGradient id="silverSwoosh" x1="0" y1="0" x2="1" y2="0">
          <stop offset="0" stop-color="#555b66"/>
          <stop offset="0.35" stop-color="#e6e6e6"/>
          <stop offset="0.6" stop-color="#8d8d8d"/>
          <stop offset="0.85" stop-color="#f4f4f4"/>
          <stop offset="1" stop-color="#9a9a9a"/>
        </linearGradient>
      </defs>
      <rect x="0" y="0" width="765" height="849" fill="url(#silverFrame)"/>
      <rect x="12" y="12" width="741" height="825" fill="var(--label-navy)"/>
      <path class="upper-band" d="M12 12 H753 V120 C560 120 300 180 12 250 Z" fill="var(--label-band)"/>
      <path class="lower-band" d="M12 680 C250 740 500 650 753 585 V650 C520 690 300 760 12 720 Z" fill="var(--label-band)"/>
      <path class="upper-swoosh" d="M12 262 C250 190 560 110 753 137 L753 149 C560 126 260 205 12 268 Z" fill="url(#silverSwoosh)"/>
      <path class="lower-swoosh" d="M12 682 C200 720 440 715 753 587 L753 598 C450 725 200 735 12 692 Z" fill="url(#silverSwoosh)"/>
    </svg>
    <div class="crest-area" role="img" aria-label="Platz für das silberne Familienwappen"></div>
    <div class="beer-style">- LAGERBIER -</div>
    <h1 class="brand-name">HEARTY<br>KANDROM</h1>
    <div class="brewery-line">BIERMANUFAKTUR WALLISER URSPRUNGS</div>
  </div>
</div>
</body>
</html>
```